Design a compelling Tarnwove Business Card that will drive people to my site

I want a business card that I can give to people—less to tell them who I am and more to direct them to my website. My website is a portal for Pelmor Aquatics Officials and a place for people who want to become Pelmor Aquatics Officials.
I am uploading my official company logo as well as a business card mockup that I did on my own. Please feel free to completely stray from this design.
I've included a screen recording of the homepage of my website as well.
Target Market(s)
Pelmor Aquatics Officials and people who desire to become one
Contact Information for Business Card
website url
Look and feel
Each slider illustrates characteristics of the customer's brand and the style your logo design should communicate.

```html
<!DOCTYPE html>
<html lang="en">
<head>
<meta charset="utf-8">
<title>Tarnwove Business Card</title>
<link rel="stylesheet" href="https://fonts.googleapis.com/css2?family=Montserrat:wght@400;500;600;700&display=swap">
<style>
  :root {
    --backdrop: #b9b9b9;
    --card: #1f1f21;
    --blue-deep: #3f5cb8;
    --blue-soft: #93a9df;
    --text-light: #ececec;
    --divider: #5a6076;
  }
  * { margin: 0; padding: 0; box-sizing: border-box; }
  html, body { width: 1200px; height: 802px; overflow: hidden; }
  body {
    background: linear-gradient(180deg, #d2d2d2 0%, var(--backdrop) 100%);
    font-family: "Montserrat", sans-serif;
    display: flex;
    align-items: center;
    justify-content: center;
    gap: 50px;
  }
  .card {
    width: 525px;
    height: 300px;
    background: var(--card);
    border-radius: 22px;
    box-shadow: 0 14px 30px rgba(0,0,0,0.35);
    position: relative;
  }
  .wordmark {
    font-weight: 700;
    color: var(--blue-soft);
    letter-spacing: -0.5px;
    display: flex;
    align-items: center;
    gap: 10px;
    white-space: nowrap;
  }
  .wordmark .dot {
    width: 14px; height: 14px;
    border-radius: 50%;
    background: var(--blue-soft);
    flex: none;
  }
  /* contact side */
  .card-contact { display: flex; align-items: center; padding: 0 34px; }
  .card-contact .wordmark { font-size: 36px; width: 220px; flex: none; }
  .card-contact .divider {
    width: 1px; height: 110px;
    background: var(--divider);
    margin: 0 26px 0 12px;
    flex: none;
  }
  .details { color: var(--text-light); white-space: nowrap; }
  .name { font-size: 21px; font-weight: 700; line-height: 1.1; }
  .name .first { color: var(--blue-deep); }
  .name .last { color: var(--blue-soft); }
  .role { font-size: 12.5px; margin-top: 3px; margin-bottom: 16px; }
  .contact-line {
    display: flex; align-items: center; gap: 8px;
    font-size: 12.5px; margin-bottom: 7px;
  }
  .contact-line svg { width: 12px; height: 12px; fill: var(--blue-deep); flex: none; }
  /* front side */
  .card-front {
    display: flex; flex-direction: column;
    align-items: center; justify-content: center;
  }
  .card-front .wordmark { font-size: 64px; margin-top: 10px; }
  .card-front .wordmark .dot { width: 20px; height: 20px; }
  .tagline {
    color: var(--text-light);
    font-size: 14px;
    font-weight: 500;
    margin-top: 40px;
  }
</style>
</head>
<body>
  <section class="card card-contact">
    <div class="wordmark"><span class="dot"></span>Tarnwove</div>
    <div class="divider"></div>
    <div class="details">
      <p class="name"><span class="first">Martin</span> <span class="last">Oswell</span></p>
      <p class="role">CEO &amp; Founder</p>
      <p class="contact-line">
        <svg viewBox="0 0 24 24"><path d="M6.6 10.8a15.1 15.1 0 0 0 6.6 6.6l2.2-2.2c.3-.3.7-.4 1-.2 1.1.4 2.3.6 3.6.6.6 0 1 .4 1 1V20c0 .6-.4 1-1 1A17 17 0 0 1 3 4c0-.6.4-1 1-1h3.5c.6 0 1 .4 1 1 0 1.3.2 2.5.6 3.6.1.3 0 .7-.2 1z"/></svg>
        (555) 201-4473
      </p>
      <p class="contact-line">
        <svg viewBox="0 0 24 24"><path d="M2 5h20v14H2zm2 2v.5l8 5 8-5V7l-8 5z"/></svg>
        martin@tarnwove.com
      </p>
      <p class="contact-line">
        <svg viewBox="0 0 24 24"><path d="M12 2a10 10 0 1 0 0 20 10 10 0 0 0 0-20zm6.9 9h-3a15 15 0 0 0-1.3-5.9A8 8 0 0 1 18.9 11zM12 4c.9 1.2 1.8 3.8 1.9 7h-3.8c.1-3.2 1-5.8 1.9-7zM9.4 5.1A15 15 0 0 0 8.1 11h-3a8 8 0 0 1 4.3-5.9zM5.1 13h3a15 15 0 0 0 1.3 5.9A8 8 0 0 1 5.1 13zM12 20c-.9-1.2-1.8-3.8-1.9-7h3.8c-.1 3.2-1 5.8-1.9 7zm2.6-1.1a15 15 0 0 0 1.3-5.9h3a8 8 0 0 1-4.3 5.9z"/></svg>
        www.tarnwove.com
      </p>
    </div>
  </section>

  <section class="card card-front">
    <div class="wordmark"><span class="dot"></span>Tarnwove</div>
    <p class="tagline">Your Poolside Officials’ Hub</p>
  </section>
</body>
</html>
```